KBT Business Cards

We require business cards for our business. We would like a matte black back to the card, with our logo centred in the middle. The front side of the card is open to design.

Target Market(s)

Clients looking for legal services (professional)

Industry/Entity Type

Legal

Contact Information for Business Card

Doran Kelbrath
Partner
Mobile: 0461 738 524
Email: doran@kbtlaw.co
Website: www.kbtlaw.co
Level 3, 118 Wendmore Street
Sydney NSW 2000

Font styles to use
Other font styles liked:
• Avenir

Colors
f04a50
ffffff
1b1b1b

Requirements
Must have
• Black back with logo included in the centre of the card.
• Our font is Avenir.

```html
<!DOCTYPE html>
<html lang="en">
<head>
<meta charset="utf-8">
<title>KBT Legal Business Cards</title>
<link rel="stylesheet" href="https://fonts.googleapis.com/css2?family=Nunito+Sans:wght@400;600;800&display=swap">
<style>
  :root {
    --brand-red: #d81e4a;
    --ink: #1b1b1b;
    --paper: #ffffff;
    --stage: #2a2a2a;
    --muted: #555555;
    --rule: #d6d6d6;
  }
  * { box-sizing: border-box; margin: 0; padding: 0; }
  html, body {
    width: 1200px; height: 960px; overflow: hidden;
    background: var(--stage);
    font-family: "Nunito Sans", "Avenir", sans-serif;
  }
  .canvas { position: relative; width: 1200px; height: 960px; }
  .card {
    position: absolute; left: 290px; width: 620px; height: 378px;
    overflow: hidden; border-radius: 4px;
    box-shadow: 0 18px 40px rgba(0,0,0,0.45);
  }
  .card--back { top: 80px; background: var(--ink); }
  .card--front { top: 502px; background: var(--paper); }

  .wordmark { display: flex; align-items: center; gap: 14px; position: absolute; }
  .wordmark__square { display: block; background: var(--brand-red); }
  .wordmark__name {
    font-weight: 800; text-transform: uppercase; letter-spacing: 0.02em; line-height: 1;
  }
  .card--back .wordmark { left: 50%; top: 50%; transform: translate(-50%, -50%); gap: 20px; }
  .card--back .wordmark__square { width: 46px; height: 46px; }
  .card--back .wordmark__name { color: var(--paper); font-size: 44px; }

  .card--front .wordmark { left: 44px; top: 86px; }
  .card--front .wordmark__square { width: 30px; height: 30px; }
  .card--front .wordmark__name { color: var(--ink); font-size: 28px; }

  .divider { position: absolute; left: 318px; top: 58px; width: 1px; height: 150px; background: var(--rule); }

  .contact { position: absolute; left: 342px; top: 64px; }
  .contact__name { color: var(--brand-red); font-weight: 800; font-size: 21px; text-transform: uppercase; letter-spacing: 0.02em; }
  .contact__role { color: var(--ink); font-size: 13px; text-transform: uppercase; letter-spacing: 0.04em; margin-bottom: 14px; }
  .contact__list { list-style: none; }
  .contact__item { display: flex; align-items: center; gap: 10px; font-size: 15px; color: var(--ink); margin-bottom: 7px; }
  .contact__icon { width: 16px; height: 16px; flex: none; }

  .wave { position: absolute; left: 0; top: 0; width: 620px; height: 378px; }
  .address {
    position: absolute; right: 60px; bottom: 12px; text-align: right;
    color: var(--paper); font-size: 15px; line-height: 1.35;
  }
</style>
</head>
<body>
<main class="canvas">
  <section class="card card--back" aria-label="Card back">
    <div class="wordmark">
      <span class="wordmark__square"></span>
      <span class="wordmark__name">KBT Legal</span>
    </div>
  </section>

  <section class="card card--front" aria-label="Card front">
    <svg class="wave" viewBox="0 0 620 378" aria-hidden="true">
      <path d="M0,168 C140,208 230,243 380,253 C500,260 585,273 620,298" fill="none" stroke="var(--brand-red)" stroke-width="2"/>
      <path d="M0,186 C140,226 230,261 380,271 C500,278 585,291 620,316" fill="none" stroke="var(--brand-red)" stroke-width="9"/>
      <path d="M0,200 C140,240 230,275 380,285 C500,292 585,305 620,330 L620,378 L0,378 Z" fill="var(--ink)"/>
    </svg>

    <div class="wordmark">
      <span class="wordmark__square"></span>
      <span class="wordmark__name">KBT Legal</span>
    </div>

    <div class="divider"></div>

    <div class="contact">
      <p class="contact__name">Doran Kelbrath</p>
      <p class="contact__role">Partner</p>
      <ul class="contact__list">
        <li class="contact__item">
          <svg class="contact__icon" viewBox="0 0 16 16" aria-hidden="true"><circle cx="8" cy="8" r="7" fill="none" stroke="var(--brand-red)" stroke-width="1.4"/><rect x="5.5" y="3.8" width="5" height="8.4" rx="1" fill="none" stroke="var(--brand-red)" stroke-width="1.2"/></svg>
          <span>0461 738 524</span>
        </li>
        <li class="contact__item">
          <svg class="contact__icon" viewBox="0 0 16 16" aria-hidden="true"><rect x="1" y="3.5" width="14" height="9" fill="var(--brand-red)"/><path d="M1,3.5 L8,9 L15,3.5" fill="none" stroke="var(--paper)" stroke-width="1.2"/></svg>
          <span>doran@kbtlaw.co</span>
        </li>
        <li class="contact__item">
          <svg class="contact__icon" viewBox="0 0 16 16" aria-hidden="true"><circle cx="8" cy="8" r="7" fill="none" stroke="var(--brand-red)" stroke-width="1.4"/><ellipse cx="8" cy="8" rx="3" ry="7" fill="none" stroke="var(--brand-red)" stroke-width="1.2"/><path d="M1,8 H15" stroke="var(--brand-red)" stroke-width="1.2"/></svg>
          <span>www.kbtlaw.co</span>
        </li>
      </ul>
    </div>

    <address class="address" style="font-style:normal">
      Level 3, 118 Wendmore Street<br>Sydney NSW 2000
    </address>
  </section>
</main>
</body>
</html>
```